Business Card Design

We are looking for a business card designed for our landscaping company. We do landscaping installation & Maintenance Services. We would like to see designs that have basic landscaping in background. We also think it is important to have both of our names and phone numbers on the card. We need something that stands out a little whether it is shape of the card or thickness or design.

Business

Bramblewood Yardworks, bramblewoodyard@mailvista.net, Owen Platt 555-273-9104, Daniel Korbin 555-618-3927

```html
<!DOCTYPE html>
<html lang="en">
<head>
<meta charset="utf-8">
<title>Bramblewood Yardworks – Business Card</title>
<link rel="stylesheet" href="https://fonts.googleapis.com/css2?family=Open+Sans:wght@400;500&display=swap">
<style>
  :root {
    --artboard: #cfcfcf;
    --card: #ffffff;
    --ink: #111111;
    --leaf: #33e633;
    --grass-dark: #4f8f22;
    --grass-light: #8cc63f;
    --stone: #b9b6ae;
    --hedge: #3f6e3a;
  }
  * { margin: 0; padding: 0; box-sizing: border-box; }
  html, body {
    width: 1200px;
    height: 754px;
    overflow: hidden;
    background: var(--artboard);
  }
  .card {
    position: absolute;
    left: 84px;
    top: 72px;
    width: 1032px;
    height: 606px;
    background: var(--card);
    overflow: hidden;
    font-family: "Open Sans", sans-serif;
  }
  .card__art {
    position: absolute;
    inset: 0;
    width: 1032px;
    height: 606px;
  }
  .brand {
    position: absolute;
    left: 60px;
    top: 143px;
    font-weight: 400;
    font-size: 74px;
    line-height: 106px;
    letter-spacing: 0.5px;
    text-transform: uppercase;
    transform: scaleX(0.92);
    transform-origin: left top;
    white-space: nowrap;
  }
  .brand__line--top { color: var(--ink); display: block; }
  .brand__line--bottom { color: var(--leaf); display: block; }
  .divider {
    position: absolute;
    left: 658px;
    top: 152px;
    width: 4px;
    height: 172px;
    background: var(--leaf);
  }
  .contacts {
    position: absolute;
    left: 687px;
    top: 152px;
    font-size: 33px;
    line-height: 38px;
    white-space: nowrap;
  }
  .contact + .contact { margin-top: 22px; }
  .contact__name { color: var(--ink); display: block; }
  .contact__phone { color: var(--leaf); display: block; }
  .email {
    position: absolute;
    left: 0;
    width: 1032px;
    top: 396px;
    text-align: center;
    font-size: 35px;
    color: var(--ink);
  }
</style>
</head>
<body>
  <main class="card">
    <svg class="card__art" viewBox="0 0 1032 606" xmlns="http://www.w3.org/2000/svg">
      <defs>
        <linearGradient id="hedgeTone" x1="0" y1="0" x2="1" y2="1">
          <stop offset="0" stop-color="#6f9a5e"/>
          <stop offset="1" stop-color="var(--hedge)"/>
        </linearGradient>
        <linearGradient id="lawnTone" x1="0" y1="0" x2="1" y2="0">
          <stop offset="0" stop-color="var(--stone)"/>
          <stop offset="0.22" stop-color="#9c9a88"/>
          <stop offset="0.35" stop-color="var(--grass-dark)"/>
          <stop offset="0.7" stop-color="var(--grass-light)"/>
          <stop offset="1" stop-color="var(--grass-dark)"/>
        </linearGradient>
      </defs>
      <polygon class="card__photo card__photo--top" role="img" aria-label="Photo of trimmed garden shrubs"
               points="53,0 201,0 127,73" fill="url(#hedgeTone)"/>
      <g class="card__photo card__photo--bottom" role="img" aria-label="Photo of a landscaped lawn with a stepping-stone path and stone patio">
        <polygon points="0,456 96,456 143,498 190,456 1032,456 1032,606 0,606" fill="url(#lawnTone)"/>
      </g>
    </svg>

    <h1 class="brand">
      <span class="brand__line--top">Bramblewood</span>
      <span class="brand__line--bottom">Yardworks</span>
    </h1>

    <div class="divider"></div>

    <section class="contacts">
      <p class="contact">
        <span class="contact__name">Owen Platt</span>
        <span class="contact__phone">555-273-9104,</span>
      </p>
      <p class="contact">
        <span class="contact__name">Daniel Korbin</span>
        <span class="contact__phone">555-618-3927</span>
      </p>
    </section>

    <p class="email">bramblewoodyard@mailvista.net</p>
  </main>
</body>
</html>
```